Dunmore Roofing

Want a professional looking business card

Industry/Entity Type

Business

Contact Information for Business Card

Paul Dunmore ( Owner) paul@dunmoreroofing-example.com, www.dunmoreroofing-example.com, Adress: 4172 Township road 43 Plantagenet,ON K9X4T2

```html
<!DOCTYPE html>
<html lang="en">
<head>
<meta charset="utf-8">
<title>Dunmore Roofing — Business Card</title>
<link rel="stylesheet" href="https://fonts.googleapis.com/css2?family=Michroma&family=Roboto:wght@400;500&display=swap">
<style>
  :root {
    --backdrop: #d9d9d9;
    --brand-blue: #1f4b8e;
    --brand-blue-dark: #1a427f;
    --silver-light: #f4f4f4;
    --silver-mid: #c9c9c9;
    --silver-edge: #9a9a9a;
    --white: #ffffff;
    --divider: rgba(255,255,255,0.35);
  }
  * { margin: 0; padding: 0; box-sizing: border-box; }
  html, body {
    width: 1200px; height: 1000px; overflow: hidden;
    background: var(--backdrop);
  }
  .stage { position: relative; width: 1200px; height: 1000px; }
  .card {
    position: absolute; left: 270px; width: 660px; height: 378px;
    box-shadow: 0 3px 10px rgba(0,0,0,0.25);
  }
  .card-front {
    top: 108px;
    background: radial-gradient(ellipse at 50% 40%, var(--silver-light) 0%, var(--silver-mid) 60%, var(--silver-edge) 100%);
    display: flex; align-items: center; justify-content: center;
  }
  .brand-name {
    font-family: "Michroma", sans-serif;
    font-weight: 400;
    text-transform: uppercase;
    letter-spacing: 2px;
    text-align: center;
    line-height: 1.35;
  }
  .card-front .brand-name { color: var(--brand-blue); font-size: 38px; }
  .card-back {
    top: 521px;
    background: linear-gradient(160deg, var(--brand-blue) 0%, var(--brand-blue-dark) 100%);
    color: var(--white);
  }
  .back-brand {
    position: absolute; left: 0; top: 0; width: 330px; height: 100%;
    display: flex; align-items: center; justify-content: center;
  }
  .card-back .brand-name { color: var(--white); font-size: 24px; }
  .divider {
    position: absolute; left: 330px; top: 120px; width: 1px; height: 150px;
    background: var(--divider);
  }
  .contact {
    position: absolute; left: 357px; top: 106px;
    font-family: "Roboto", sans-serif; font-size: 14.5px; line-height: 19px;
  }
  .contact-name {
    font-family: "Michroma", sans-serif; font-size: 15px; letter-spacing: 1px;
    text-transform: uppercase;
  }
  .contact-role { margin-bottom: 14px; }
  .contact-address { margin-bottom: 12px; }
  .contact-line { display: flex; align-items: center; gap: 5px; height: 21px; }
  .contact-line svg { width: 11px; height: 11px; fill: var(--white); flex: none; }
</style>
</head>
<body>
<main class="stage">
  <section class="card card-front" aria-label="Business card front">
    <p class="brand-name">Dunmore<br>Roofing</p>
  </section>

  <section class="card card-back" aria-label="Business card back">
    <div class="back-brand">
      <p class="brand-name">Dunmore<br>Roofing</p>
    </div>
    <div class="divider"></div>
    <div class="contact">
      <p class="contact-name">Paul Dunmore</p>
      <p class="contact-role">Owner</p>
      <p class="contact-address">4172 Township road 43<br>Plantagenet, ON K9X4T2</p>
      <p class="contact-line">
        <svg viewBox="0 0 24 24" aria-hidden="true"><path d="M6.6 10.8a15 15 0 0 0 6.6 6.6l2.2-2.2a1 1 0 0 1 1-.25 11.4 11.4 0 0 0 3.6.57 1 1 0 0 1 1 1V20a1 1 0 0 1-1 1A17 17 0 0 1 3 4a1 1 0 0 1 1-1h3.5a1 1 0 0 1 1 1c0 1.25.2 2.45.57 3.57a1 1 0 0 1-.25 1z"/></svg>
        123.456.7890
      </p>
      <p class="contact-line">
        <svg viewBox="0 0 24 24" aria-hidden="true"><path d="M2 5h20v14H2z M2 5l10 8 10-8" fill="none" stroke="#fff" stroke-width="2.4"/></svg>
        paul@dunmoreroofing-example.com
      </p>
      <p class="contact-line">
        <svg viewBox="0 0 24 24" aria-hidden="true"><circle cx="10" cy="10" r="6.5" fill="none" stroke="#fff" stroke-width="3"/><path d="M15 15l6 6" stroke="#fff" stroke-width="3"/></svg>
        www.dunmoreroofing-example.com
      </p>
    </div>
  </section>
</main>
</body>
</html>
```